wardrobe/costume stylist needs good business card for own business

Hi:)

I'm wanting a business card for my company. I am a freelance stylist.

I do wardrobe/costume stylist to TV commercials; Films; Fashion and Lifestyle shoots.

I'd like a design based around my name Rosalind Parfrey written nicely, maybe a colour? Up to you?!

I've attached a couple of images of business cards I like
.... be creative and have fun!

Thank you :)

Reason: I was trying to get my new business card ready for before I headed overseas Friday morning but I don't think that was realistic so I'd like to extend the deadline to give time to the project. Thank you

Hi designers:) Thank you for all your designs, I've extended the deadline until Sunday, so there's a bit more time. I've attached 3 pictures of business cards which I quite like, please take a look to see if it can be of help in your process. I like the pale plain or patterned background with dark font and the dark plain or patterned background with the pale font the motifs the feminine fonts the plain fonts I like the idea of playing with a circle or some shape on one side of the card with my name or initials as in the picture I have on my post could you play around with this idea a bit please? Thank you all for the work you've done :) Rosa

Hi I am working overseas til Saturday night sorry for no feedback until I teturn Thanks :) Rosa

Hi designers, Thank you all so much for submitting your designs, I really appreciate your input into my project :) I'm sorry I didn't get to respond to some comments, and give feedback. I didn't back from being away until later than I expected, and the deadline had passed then, so apologies. Thanks to you all again for all your really good designs :) Rosa

Target Market(s)

I am a freelance stylist my target audience is producers, production companies, photographers, directors...

Industry/Entity Type

Business

Requirements
Must have
• Rosalind Parfrey
Stylist or Wardrobe Stylist

email rosaparfrey@mailbox-example.co.nz
Mobile 0218467193

(Don't have to use the words 'email' and 'mobile')
Nice to have
• Would like it to be double sided
Like B & W
Like pale colour background with dark font or white font
Like dark colour background with pale font
Should not have
• I would prefer it not to incorporate pictures

```html
<!DOCTYPE html>
<html lang="en">
<head>
<meta charset="utf-8">
<title>Rosalind Parfrey – Wardrobe Stylist Business Card</title>
<link rel="stylesheet" href="https://fonts.googleapis.com/css2?family=Arimo:wght@400;700&display=swap">
<style>
  :root {
    --page-bg: #e9e9ea;
    --card-bg: #1d1c1e;
    --card-bg-edge: #151416;
    --accent-blue: #29b6ea;
    --text-white: #ffffff;
    --text-soft: #d9d9d9;
  }
  * { box-sizing: border-box; margin: 0; padding: 0; }
  html, body {
    width: 1200px;
    height: 533px;
    overflow: hidden;
    background: var(--page-bg);
    font-family: "Arimo", Arial, sans-serif;
  }
  .sheet {
    width: 1200px;
    height: 533px;
    display: flex;
    align-items: center;
    justify-content: center;
    gap: 24px;
  }
  .card {
    position: relative;
    width: 570px;
    height: 326px;
    background: radial-gradient(ellipse at 50% 40%, var(--card-bg) 60%, var(--card-bg-edge) 100%);
    overflow: hidden;
    box-shadow: 0 2px 6px rgba(0,0,0,0.18);
  }

  /* Front */
  .accent-bar {
    position: absolute;
    left: 30px;
    top: 0;
    width: 20px;
    height: 158px;
    background: var(--accent-blue);
  }
  .brand {
    position: absolute;
    top: 38px;
    right: 28px;
    display: flex;
    align-items: center;
    gap: 12px;
  }
  .brand-dot {
    width: 40px;
    height: 40px;
    border-radius: 50%;
    border: 3px solid var(--accent-blue);
  }
  .brand-name {
    color: var(--accent-blue);
    font-size: 29px;
    font-weight: 700;
    letter-spacing: -0.3px;
  }
  .identity {
    position: absolute;
    left: 30px;
    top: 166px;
  }
  .person-name {
    color: var(--text-white);
    font-size: 19px;
    font-weight: 700;
    letter-spacing: -0.6px;
    text-transform: uppercase;
  }
  .person-role {
    margin-top: 3px;
    color: var(--text-soft);
    font-size: 11px;
    letter-spacing: 0.2px;
    text-transform: uppercase;
  }
  .contacts {
    position: absolute;
    left: 30px;
    top: 236px;
    list-style: none;
  }
  .contact {
    display: flex;
    align-items: center;
    gap: 12px;
    margin-bottom: 8px;
    color: var(--text-white);
    font-size: 14px;
  }
  .contact-icon {
    width: 28px;
    height: 28px;
    background: var(--accent-blue);
    display: flex;
    align-items: center;
    justify-content: center;
  }

  /* Back */
  .card-back {
    display: flex;
    flex-direction: column;
    align-items: center;
    justify-content: center;
    gap: 14px;
  }
  .back-ring {
    width: 96px;
    height: 96px;
    border-radius: 50%;
    border: 5px solid var(--accent-blue);
  }
  .back-name {
    color: var(--accent-blue);
    font-size: 22px;
    font-weight: 700;
  }
</style>
</head>
<body>
<main class="sheet">
  <section class="card card-front" aria-label="Card front">
    <div class="accent-bar"></div>
    <div class="brand">
      <span class="brand-dot"></span>
      <span class="brand-name">Rosalind Parfrey</span>
    </div>
    <div class="identity">
      <h1 class="person-name">Rosalind Parfrey</h1>
      <p class="person-role">Wardrobe Stylist</p>
    </div>
    <ul class="contacts">
      <li class="contact">
        <span class="contact-icon">
          <svg width="18" height="13" viewBox="0 0 18 13" aria-hidden="true">
            <rect x="0.75" y="0.75" width="16.5" height="11.5" fill="none" stroke="#fff" stroke-width="1.5"/>
            <polyline points="1,1 9,7.5 17,1" fill="none" stroke="#fff" stroke-width="1.5"/>
          </svg>
        </span>
        <span class="contact-text">rosaparfrey@mailbox-example.co.nz</span>
      </li>
      <li class="contact">
        <span class="contact-icon">
          <svg width="11" height="18" viewBox="0 0 11 18" aria-hidden="true">
            <rect x="0.75" y="0.75" width="9.5" height="16.5" rx="1.5" fill="none" stroke="#fff" stroke-width="1.5"/>
            <rect x="2.5" y="3" width="6" height="9" fill="#fff"/>
            <circle cx="5.5" cy="14.5" r="1" fill="#fff"/>
          </svg>
        </span>
        <span class="contact-text">0218467193</span>
      </li>
    </ul>
  </section>

  <section class="card card-back" aria-label="Card back">
    <span class="back-ring"></span>
    <span class="back-name">Rosalind Parfrey</span>
  </section>
</main>
</body>
</html>
```